New Business Card Design Project

I need a design for business cards, i am an electrical business called "Corvane Electrical and Communications" i need the cards to be double sided with the company logo on the back (attached) the front needs to say my company name, web site, email address, telephone number, and ABN number and electrical license number. I am open to different arrangements of the information but would like the background to be incorporating something electrical or something that looks smart. open to all additional ideas also.

The company colours are orange and grey see logo attached.

Business Name: Corvane Electrical and Communications
Website: corvaneelectricalandcomms.example.com.au
Email: brent@corvaneelectricalandcomms.example.com.au
Telephone(mobile): 0481209736
ABN: 71208349162
Lic No: 418273D

Target Market(s)

Business entities, Project Managers, Accounts, Clients

Industry/Entity Type

Electrician

Contact Information for Business Card

I need a design for business cards, i am an electrical business called "Corvane Electrical and Communications" i need the cards to be double sided with the company logo on the back (attached) the front needs to say my company name

Font styles to use
Serif
Sans Serif

Colors
f37122
5c5c5c

Requirements
Must have
• Must have the Logo on the back open to different ways of it being on the back but had in mind to keep it central but again open to other options
Nice to have
• A real modern cool background that is eye catching yet contemporary
Should not have
• No backgrounds of a light bulb or plug or anything like that

```html
<!DOCTYPE html>
<html lang="en">
<head>
<meta charset="utf-8">
<title>Corvane Electrical and Communications – Business Cards</title>
<link href="https://fonts.googleapis.com/css2?family=Open+Sans:wght@400;600;700&display=swap" rel="stylesheet">
<style>
  :root {
    --orange: #f5a41c;
    --orange-deep: #f37122;
    --grey: #5c5c5c;
    --grey-dark: #4f4f4f;
    --white: #ffffff;
    --page: #2b2b2b;
  }
  * { box-sizing: border-box; margin: 0; padding: 0; }
  html, body { width: 1200px; height: 900px; overflow: hidden; }
  body {
    background: var(--page);
    font-family: "Open Sans", Arial, sans-serif;
    position: relative;
  }
  .card {
    position: absolute;
    width: 620px;
    height: 354px;
    border-radius: 22px;
    overflow: hidden;
    background: var(--grey);
    box-shadow: 0 14px 30px rgba(0,0,0,.45);
  }
  .card-back { left: 110px; top: 80px; }
  .card-front { left: 470px; top: 466px; }

  /* back */
  .back-band {
    position: absolute; left: 0; right: 0; top: 248px; height: 44px;
    background: var(--white);
    display: flex; align-items: center; justify-content: center;
    font-size: 17px; font-weight: 600; color: var(--grey-dark); letter-spacing: .2px;
  }
  .back-band .accent { color: var(--orange); }
  .brand-back {
    position: absolute; left: 0; right: 0; top: 72px;
    display: flex; flex-direction: column; align-items: center;
    color: var(--white);
  }
  .brand-back .brand-row { display: flex; align-items: center; gap: 14px; }
  .brand-dot { width: 22px; height: 22px; border-radius: 50%; background: var(--orange); }
  .brand-back .brand-name {
    font-size: 70px; font-weight: 600; letter-spacing: 4px; line-height: 1; text-transform: uppercase;
  }
  .brand-back .brand-sub {
    margin-top: 12px; font-size: 18px; font-weight: 600; letter-spacing: 2.4px; text-transform: uppercase;
  }

  /* front */
  .front-art { position: absolute; inset: 0; }
  .brand-front {
    position: absolute; right: 36px; top: 46px; width: 330px;
    display: flex; flex-direction: column; align-items: center;
    color: var(--grey-dark);
  }
  .brand-front .brand-row { display: flex; align-items: center; gap: 10px; }
  .brand-front .brand-dot { width: 16px; height: 16px; }
  .brand-front .brand-name {
    font-size: 50px; font-weight: 600; letter-spacing: 3px; line-height: 1; text-transform: uppercase;
  }
  .brand-front .brand-sub {
    margin-top: 8px; font-size: 12.5px; font-weight: 600; letter-spacing: 1.8px; text-transform: uppercase;
  }
  .licence {
    margin-top: 10px; font-size: 13px; color: var(--grey-dark);
  }
  .licence .accent { color: var(--orange); }

  .holder { position: absolute; left: 30px; top: 214px; color: var(--white); }
  .holder-name {
    font-size: 24px; font-weight: 400; color: var(--orange); letter-spacing: .5px; text-transform: uppercase; line-height: 1;
  }
  .holder-rule {
    position: absolute; left: 150px; top: 32px; width: 300px; height: 2px; background: var(--orange);
  }
  .holder-role { margin-top: 6px; font-size: 12px; letter-spacing: .5px; text-transform: uppercase; }
  .abn { margin-top: 10px; font-size: 13px; }
  .abn .label { color: var(--orange); font-weight: 600; }
  .contacts { list-style: none; margin-top: 6px; font-size: 13px; }
  .contacts li { display: flex; align-items: center; gap: 9px; line-height: 19px; }
  .contacts svg { width: 11px; height: 11px; flex: none; }
</style>
</head>
<body>

<section class="card card-back" aria-label="Card back">
  <div class="brand-back">
    <div class="brand-row">
      <span class="brand-dot"></span>
      <span class="brand-name">Corvane</span>
    </div>
    <span class="brand-sub">Electrical &amp; Communications</span>
  </div>
  <div class="back-band">www.<span class="accent">corvaneelectricalandcomms</span>.example.com.au</div>
</section>

<section class="card card-front" aria-label="Card front">
  <svg class="front-art" viewBox="0 0 620 354" width="620" height="354" aria-hidden="true">
    <path d="M170 0 Q250 245 620 236 L620 0 Z" fill="var(--white)"/>
    <path d="M150 0 Q225 262 620 242 L620 236 Q250 245 170 0 Z" fill="var(--orange)"/>
  </svg>

  <div class="brand-front">
    <div class="brand-row">
      <span class="brand-dot"></span>
      <span class="brand-name">Corvane</span>
    </div>
    <span class="brand-sub">Electrical &amp; Communications</span>
    <p class="licence">Lic No: <span class="accent">418273D</span></p>
  </div>

  <div class="holder">
    <p class="holder-name">Marlo Keswick</p>
    <span class="holder-rule"></span>
    <p class="holder-role">Director</p>
    <p class="abn"><span class="label">ABN:</span> 71208349162</p>
    <ul class="contacts">
      <li>
        <svg viewBox="0 0 24 24"><path fill="var(--orange)" d="M6.6 10.8a15 15 0 0 0 6.6 6.6l2.2-2.2a1 1 0 0 1 1-.25 11.4 11.4 0 0 0 3.6.57 1 1 0 0 1 1 1V20a1 1 0 0 1-1 1A17 17 0 0 1 3 4a1 1 0 0 1 1-1h3.5a1 1 0 0 1 1 1c0 1.25.2 2.45.57 3.57a1 1 0 0 1-.25 1z"/></svg>
        0481-209-736
      </li>
      <li>
        <svg viewBox="0 0 24 24"><rect x="2" y="5" width="20" height="14" rx="1.5" fill="none" stroke="var(--orange)" stroke-width="2.4"/><path d="M3 6l9 7 9-7" fill="none" stroke="var(--orange)" stroke-width="2.4"/></svg>
        brent@corvaneelectricalandcomms.example.com.au
      </li>
      <li>
        <svg viewBox="0 0 24 24"><circle cx="12" cy="12" r="10" fill="var(--orange)"/></svg>
        www.corvaneelectricalandcomms.example.com.au
      </li>
    </ul>
  </div>
</section>

</body>
</html>
```